RTavenor Business Cards & Letterhead

I have a logo but need a design for some new business cards. We are a Design-Build Firm that specializes in the design and construction of commercial projects.
the cards need to be professional. no cartoon stuff.
i would like to have the cards in AI format so I can update the card as needed. Logo is provided.
Our Address is: 4187 Marlowe Ct. Brandon Mills, Ohio 27614

```html
<!DOCTYPE html>
<html lang="en">
<head>
<meta charset="utf-8">
<title>RTavenor Business Card</title>
<link href="https://fonts.googleapis.com/css2?family=Open+Sans:wght@400;600;700&display=swap" rel="stylesheet">
<style>
  :root {
    --backdrop: #323232;
    --card-white: #ffffff;
    --brand-blue: #1670b0;
    --brand-blue-deep: #0b3f68;
    --brand-blue-light: #1582c8;
    --brand-grey: #6d6e71;
    --ink: #1d1d1d;
    --back-glow: #1479bb;
    --back-edge: #0a3a61;
  }
  * { box-sizing: border-box; margin: 0; padding: 0; }
  html, body { width: 1200px; height: 780px; overflow: hidden; }
  body {
    background: var(--backdrop);
    font-family: "Open Sans", Arial, sans-serif;
    display: flex;
    align-items: center;
    justify-content: center;
    gap: 40px;
  }
  .card {
    position: relative;
    width: 540px;
    height: 309px;
    overflow: hidden;
    box-shadow: 0 10px 26px rgba(0,0,0,0.45);
  }
  /* Back side */
  .card-back {
    background: radial-gradient(ellipse at 52% 55%, var(--back-glow) 0%, #11598f 40%, var(--back-edge) 85%);
    display: flex;
    align-items: center;
    justify-content: center;
  }
  .card-back .wordmark {
    font-weight: 700;
    font-size: 58px;
    letter-spacing: 2px;
    color: #0e4a78;
  }
  /* Front side */
  .card-front { background: var(--card-white); }
  .card-front .wordmark {
    position: absolute;
    top: 52px;
    left: 150px;
    display: flex;
    align-items: center;
    gap: 10px;
    font-weight: 700;
    font-size: 46px;
    letter-spacing: 1px;
    color: var(--brand-grey);
  }
  .wordmark .mark-square {
    width: 28px; height: 28px;
    background: var(--brand-blue);
  }
  .wordmark .reg { font-size: 13px; font-weight: 400; align-self: flex-start; margin-top: 6px; margin-left: -4px; }
  .identity {
    position: absolute;
    left: 20px;
    top: 152px;
    width: 262px;
    text-align: right;
  }
  .identity .person {
    font-weight: 700;
    font-size: 23px;
    color: var(--brand-blue);
    letter-spacing: 0.5px;
    line-height: 1.15;
  }
  .identity .role {
    font-weight: 600;
    font-size: 14px;
    color: var(--ink);
  }
  .divider {
    position: absolute;
    left: 294px;
    top: 136px;
    width: 1px;
    height: 84px;
    background: #444;
  }
  .contacts {
    position: absolute;
    left: 310px;
    top: 138px;
    list-style: none;
    font-size: 14px;
    color: var(--ink);
    line-height: 25px;
  }
  .contacts li { display: flex; align-items: center; gap: 8px; }
  .contacts svg { width: 14px; height: 14px; flex: none; }
  .icon-fill { fill: var(--brand-blue); }
  .icon-line { fill: none; stroke: var(--brand-blue); stroke-width: 2.4; stroke-linejoin: round; }
  .address-band {
    position: absolute;
    left: 0; right: 0;
    top: 234px;
    height: 30px;
    background: linear-gradient(90deg, var(--brand-blue-light), var(--brand-blue-deep));
    color: #fff;
    font-size: 14px;
    font-weight: 400;
    display: flex;
    align-items: center;
    justify-content: center;
    letter-spacing: 0.3px;
  }
</style>
</head>
<body>
  <section class="card card-back">
    <div class="wordmark">RTAVENOR</div>
  </section>

  <section class="card card-front">
    <div class="wordmark"><span class="mark-square"></span>RTAVENOR<span class="reg">®</span></div>

    <div class="identity">
      <div class="person">MARCUS TAVENOR</div>
      <div class="role">Founder/President</div>
    </div>

    <div class="divider"></div>

    <ul class="contacts">
      <li>
        <svg viewBox="0 0 24 24" aria-hidden="true"><path class="icon-fill" d="M6.6 10.8a15.1 15.1 0 0 0 6.6 6.6l2.2-2.2c.3-.3.7-.4 1-.2 1.1.4 2.3.6 3.6.6.6 0 1 .4 1 1V20c0 .6-.4 1-1 1A17 17 0 0 1 3 4c0-.6.4-1 1-1h3.5c.6 0 1 .4 1 1 0 1.3.2 2.5.6 3.6.1.3 0 .7-.2 1z"/></svg>
        (555) 014-8237
      </li>
      <li>
        <svg viewBox="0 0 24 24" aria-hidden="true"><circle class="icon-line" cx="12" cy="12" r="9.5"/><path class="icon-line" d="M2.5 12h19M12 2.5c3 3 3 16 0 19M12 2.5c-3 3-3 16 0 19"/></svg>
        www.rtavenor.com
      </li>
      <li>
        <svg viewBox="0 0 24 24" aria-hidden="true"><rect class="icon-line" x="2.5" y="5.5" width="19" height="13"/><path class="icon-line" d="M2.5 5.5l9.5 7 9.5-7"/></svg>
        MT@RTavenor.com
      </li>
    </ul>

    <div class="address-band">4187 Marlowe Ct. Brandon Mills, Ohio 27614</div>
  </section>
</body>
</html>
```